New tech executive consulting company needs professionally branded document templates

We are a new business selling fractional board advisory and go-to-market consulting services into the Technology space. Tessaly Brink are experts in providing high-quality executive-level leaders on a part-time basis to tech companies in need of their expertise. We work closely with clients to understand their business needs, challenges, and goals, and provides customised solutions to help them succeed. Due to our audience we need the design to have a high quality, executive look and feel.

Our first website is live and can be found at tessalybrink.example. We also already have a logo which I've uploaded. Our brand is clean and uses orange to give it colour and an identity that stands out.

We need some document master templates created so we can create our own presentations (Google Slides & Powerpoint), PDF documents, and Word templates, and ideally also a LinkedIn banner.

```html
<!DOCTYPE html>
<html lang="en">
<head>
<meta charset="utf-8">
<title>Tessaly Brink – Presentation Templates</title>
<link href="https://fonts.googleapis.com/css2?family=Oswald:wght@500;600;700&family=Poppins:wght@400;500&display=swap" rel="stylesheet">
<style>
:root{
  --orange:#f07022;
  --navy:#2a3440;
  --ink:#2b2b2b;
  --text:#3c3c3c;
  --canvas:#7b7b7b;
  --light:#f1f1f1;
  --white:#ffffff;
  --tile-line:#dcdcdc;
}
*{box-sizing:border-box;margin:0;padding:0}
html,body{width:1200px;height:4079px;overflow:hidden}
body{background:var(--canvas);position:relative;font-family:"Poppins",sans-serif;color:var(--text)}
.slide{position:absolute;left:24px;width:1152px;height:648px;overflow:hidden;background:var(--white)}
.abs{position:absolute}
.fill{position:absolute;inset:0}
.display{font-family:"Oswald",sans-serif;font-weight:700;text-transform:uppercase;letter-spacing:0}
.orange{color:var(--orange)}
.navy{color:var(--navy)}
.brand-mark{position:absolute;font-family:"Oswald",sans-serif;font-weight:600;color:var(--navy);letter-spacing:2px;text-transform:uppercase;white-space:nowrap}
.brand-small{right:26px;bottom:20px;font-size:14px}
.overlay{position:absolute;inset:0;width:100%;height:100%}

/* slide 1 */
.hero{top:28px;background:linear-gradient(135deg,#f7f7f7,#e6e6e6)}
.hero-photo{clip-path:polygon(0 0,728px 0,482px 648px,0 648px);background:linear-gradient(160deg,#c9d0d3,#8b8a83 55%,#4e4a45)}
.hero-brand{right:40px;top:130px;font-size:26px}
.hero-title{right:36px;top:210px;text-align:right;font-size:46px;line-height:56px}
.hero-copy{right:36px;top:404px;width:380px;text-align:right;font-size:13px;line-height:23px;color:var(--text)}

/* slide 2 */
.about{top:698px;background:radial-gradient(circle at 10% 90%,#ececec,#ffffff 55%)}
.about-photo{clip-path:polygon(704px 11px,1141px 11px,1141px 639px,452px 639px);background:linear-gradient(150deg,#d9d7d0,#8b7e6f 50%,#3e3b38)}
.about-card{left:52px;top:79px;width:641px;height:489px;background:var(--white);box-shadow:0 4px 18px rgba(0,0,0,.12);padding:50px 56px 0 34px}
.eyebrow{font-family:"Oswald",sans-serif;font-weight:600;font-size:16px;color:var(--ink);text-transform:uppercase}
.about-title{font-size:35px;line-height:44px;margin:6px 0 16px}
.about-card p{font-size:16px;line-height:28px;color:var(--text);margin-bottom:6px}

/* slide 3 */
.founder{top:1368px;background:linear-gradient(120deg,#ffffff 40%,#ececec)}
.founder-panel{clip-path:polygon(19px 24px,364px 24px,657px 623px,19px 623px);background:linear-gradient(135deg,#f07a2c,#e8651a)}
.founder-portrait{left:308px;top:127px;width:383px;height:360px;border-radius:14px;background:linear-gradient(160deg,#6b4a35,#c79a7a 45%,#2c4d85)}
.founder-name{left:744px;top:138px;font-size:40px;line-height:50px}
.founder-copy{left:744px;top:196px;width:368px;font-size:12.5px;line-height:24px;text-align:justify}
.founder-copy p+p{margin-top:2px}

/* slide 4 */
.cta{top:2037px}
.cta-photo{top:0;left:0;width:1152px;height:582px;background:linear-gradient(100deg,#aab7c0,#53606c 30%,#c9d1d6 65%,#6c7884)}
.cta-band{clip-path:polygon(411px 0,788px 0,680px 582px,301px 582px);background:var(--orange)}
.cta-text{left:340px;top:158px;width:400px;text-align:center;color:var(--white);font-size:35px;line-height:49px}

/* slide 5 */
.partners{top:2707px;background:#f4f4f4}
.partners-band{left:0;top:0;width:1152px;height:190px;background:var(--navy)}
.partners-eyebrow{left:0;width:1152px;top:38px;text-align:center;font-size:17px;font-weight:600}
.partners-title{left:0;width:1152px;top:60px;text-align:center;font-size:38px;color:var(--white)}
.partners-panel{left:47px;top:166px;width:1058px;height:482px;background:var(--white)}
.partners-lead{left:90px;top:190px;width:972px;text-align:center;font-size:15.5px;line-height:28px;color:var(--ink)}
.tile{position:absolute;width:211px;height:82px;border:1px solid var(--tile-line);background:var(--white);display:flex;align-items:center;justify-content:center;gap:10px}
.tile .dot{width:30px;height:30px;border-radius:50%;background:#9a9a9a}
.tile .bar{width:80px;height:10px;background:#c4c4c4}

/* slide 6 */
.contact{top:3377px;background:radial-gradient(circle at 0 0,#e9e9e9,#ffffff 50%)}
.contact-photo{clip-path:polygon(475px 0,1152px 0,1152px 648px,736px 648px);background:linear-gradient(170deg,#eef0ef,#b8b4a4 50%,#5b5750)}
.contact-brand{left:87px;top:128px;font-size:42px;line-height:46px;letter-spacing:4px}
.contact-title{left:87px;top:258px;font-size:32px;color:var(--ink)}
.contact-item{position:absolute;left:87px;display:flex;align-items:flex-start;gap:18px}
.contact-icon{width:38px;height:38px;border-radius:50%;background:var(--orange);display:flex;align-items:center;justify-content:center;flex:none}
.contact-label{font-family:"Oswald",sans-serif;font-weight:600;font-size:19px;color:var(--ink);text-transform:uppercase;line-height:24px}
.contact-value{font-size:14px;color:var(--ink);line-height:22px}
.brand-light{color:var(--white)}
</style>
</head>
<body>

<!-- Cover -->
<section class="slide hero">
  <div class="fill hero-photo" role="img" aria-label="Photo of three colleagues reviewing documents around a laptop in a bright office"></div>
  <svg class="overlay" viewBox="0 0 1152 648" aria-hidden="true">
    <polygon points="728,0 762,0 516,648 482,648" fill="var(--orange)"/>
    <line x1="475" y1="149" x2="772" y2="556" stroke="var(--navy)" stroke-width="13"/>
  </svg>
  <div class="brand-mark hero-brand">Tessaly Brink</div>
  <h1 class="abs display hero-title"><span class="orange">Expertsin Providing</span><br><span class="navy">Executive Leadership</span><br><span class="navy">On Demand</span></h1>
  <p class="abs hero-copy">Tessaly Brink are experts in providing high-quality executive-level leaders on a part-time basis to tech companies in need of their expertise. We work closely with clients to understand their business needs,</p>
</section>

<!-- About -->
<section class="slide about">
  <div class="fill about-photo" role="img" aria-label="Photo of a business team meeting at a long table in a glass-walled boardroom"></div>
  <svg class="overlay" viewBox="0 0 1152 648" aria-hidden="true">
    <polygon points="704,11 722,11 470,639 452,639" fill="var(--orange)"/>
  </svg>
  <div class="abs about-card">
    <div class="eyebrow">About Us</div>
    <h2 class="display about-title"><span class="orange">The Smart Way To</span> <span class="navy">Scale Your Business</span></h2>
    <p>Tessaly Brink are experts in providing high-quality executive-level leaders on a part-time basis to tech companies in need of their expertise. We work closely with clients to understand their business needs, challenges, and goals, and provides customised solutions to help them succeed.</p>
    <p>Our strategic insights, leadership, and collaborative approach make us a valuable partner for companies looking to drive growth and innovation. We are passionate about helping companies achieve their goals and are committed to providing the highest level of service to our clients.</p>
  </div>
  <div class="brand-mark brand-small">Tessaly Brink</div>
</section>

<!-- Founder -->
<section class="slide founder">
  <div class="fill founder-panel" role="img" aria-label="Orange-tinted photo of colleagues working together"></div>
  <div class="abs founder-portrait" role="img" aria-label="Portrait photo of the founder, Rowan Pike"></div>
  <h2 class="abs display founder-name"><span class="orange">Rowan</span> <span class="navy">Pike</span></h2>
  <div class="abs founder-copy">
    <p>Rowan Pike is a highly accomplished business leader with extensive experience in executive-level leadership and strategy. As the founder of Tessaly Brink, Rowan brings his years of experience in the technology industry to help companies achieve their goals.</p>
    <p>Throughout his career, Rowan has held executive positions in companies ranging from startups to large corporations. He has a deep understanding of the tech industry and has helped companies at all stages of maturity drive significant growth and innovation.</p>
  </div>
  <div class="brand-mark brand-small">Tessaly Brink</div>
</section>

<!-- Call to action -->
<section class="slide cta">
  <div class="abs cta-photo" role="img" aria-label="Photo of a smiling team in a meeting around a conference table"></div>
  <div class="fill cta-band"></div>
  <p class="abs display cta-text">Let us help you take your business to the next level. Contact us for a free consultation.</p>
  <div class="brand-mark brand-small">Tessaly Brink</div>
</section>

<!-- Partners -->
<section class="slide partners">
  <div class="abs partners-band"></div>
  <div class="abs display orange partners-eyebrow">Tech Companies</div>
  <h2 class="abs display partners-title">Our Partners</h2>
  <div class="abs partners-panel"></div>
  <p class="abs partners-lead">Lorem ipsum dolor sit amet, consectetur adipiscing elit, sed do eiusmod tempor incididunt ut labore et dolore magna aliqua. Quis ipsum suspendisse ultrices gravida. Risus commodo viverra maecenas accumsan lacus vel facilisis.</p>
  <div class="tile" style="left:108px;top:280px"><span class="dot"></span><span class="bar"></span></div>
  <div class="tile" style="left:365px;top:280px"><span class="dot"></span><span class="bar"></span></div>
  <div class="tile" style="left:623px;top:280px"><span class="dot"></span><span class="bar"></span></div>
  <div class="tile" style="left:881px;top:280px"><span class="dot"></span><span class="bar"></span></div>
  <div class="tile" style="left:108px;top:389px"><span class="dot"></span><span class="bar"></span></div>
  <div class="tile" style="left:365px;top:389px"><span class="dot"></span><span class="bar"></span></div>
  <div class="tile" style="left:623px;top:389px"><span class="dot"></span><span class="bar"></span></div>
  <div class="tile" style="left:881px;top:389px;background:#f0f0f0"><span class="dot"></span><span class="bar"></span></div>
  <div class="tile" style="left:108px;top:498px"><span class="dot"></span><span class="bar"></span></div>
  <div class="tile" style="left:365px;top:498px;border-color:#8a8a8a"><span class="dot"></span><span class="bar"></span></div>
  <div class="tile" style="left:623px;top:498px"><span class="dot"></span><span class="bar"></span></div>
  <div class="tile" style="left:881px;top:498px"><span class="dot"></span><span class="bar"></span></div>
  <div class="brand-mark brand-small">Tessaly Brink</div>
</section>

<!-- Contact -->
<section class="slide contact">
  <div class="fill contact-photo" role="img" aria-label="Photo of two businesswomen shaking hands in a bright office"></div>
  <svg class="overlay" viewBox="0 0 1152 648" aria-hidden="true">
    <polygon points="459,0 475,0 736,648 720,648" fill="var(--orange)"/>
    <line x1="435" y1="546" x2="728" y2="130" stroke="var(--navy)" stroke-width="13"/>
  </svg>
  <div class="brand-mark contact-brand">Tessaly<br>Brink</div>
  <h2 class="abs display contact-title">Contact Us</h2>
  <div class="contact-item" style="top:338px">
    <span class="contact-icon"><svg width="18" height="18" viewBox="0 0 24 24" aria-hidden="true"><path d="M12 2a7 7 0 0 0-7 7c0 5 7 13 7 13s7-8 7-13a7 7 0 0 0-7-7zm0 9.5A2.5 2.5 0 1 1 12 6.5a2.5 2.5 0 0 1 0 5z" fill="#fff"/></svg></span>
    <div><div class="contact-label">Location:</div><div class="contact-value">25, Harbour Row Lorem 0621</div></div>
  </div>
  <div class="contact-item" style="top:414px">
    <span class="contact-icon"><svg width="18" height="18" viewBox="0 0 24 24" aria-hidden="true"><path d="M6.6 10.8a15 15 0 0 0 6.6 6.6l2.2-2.2a1 1 0 0 1 1-.25 11.4 11.4 0 0 0 3.6.57 1 1 0 0 1 1 1V20a1 1 0 0 1-1 1A17 17 0 0 1 3 4a1 1 0 0 1 1-1h3.5a1 1 0 0 1 1 1c0 1.25.2 2.45.57 3.6a1 1 0 0 1-.25 1z" fill="#fff"/></svg></span>
    <div><div class="contact-label">Phone Number</div><div class="contact-value">+44 7700 900123</div></div>
  </div>
  <div class="contact-item" style="top:498px">
    <span class="contact-icon"><svg width="18" height="18" viewBox="0 0 24 24" aria-hidden="true"><rect x="3" y="6" width="18" height="12" rx="2" fill="#fff"/><path d="M3.5 7l8.5 6 8.5-6" stroke="var(--orange)" stroke-width="1.8" fill="none"/></svg></span>
    <div><div class="contact-label">Email Address</div><div class="contact-value">info@tessalybrink.example</div></div>
  </div>
  <div class="brand-mark brand-small brand-light">Tessaly Brink</div>
</section>

</body>
</html>
```